Summit Bodyform Gym Website

We need a website design for our gym.

Summit is the UAE's first calisthenics and parkour gym. The theme under which the gym revolves is that one does not require any machinery to workout as our bodies could be themselves the machinery. The gym is designed to be the more of a social hub rather than an "in-and-out" gym, where people come train, have fun, hang out and socialize for a few hours rather than just train for 60 minutes then leave. The gym is designed to be a big open space with lots of natural sunlight, natural wood and plants all over the place to create a natural and refreshing setting. We also use recycled material throughout the gym and recycle our waste as being green is part of our philosophy. We currently also have some of the world's top and most recognized calisthenics athletes working with us.

We would like our website to reflect all that as well as provide a simple, interactive and fun way for visitors to be able to get class and gym information, check out gym media and contact us for bookings.

Target Market(s)

Ages 15-35

Industry/Entity Type

Fitness

Coding

Coded - Design and coding required

Number of Pages Required

4 page

Font styles to use
Decorative

Colors
0792cd

Requirements
Must have
• Class descriptions
• Gym description
• Class schedules
• Trainer profiles
• Gym philosophy
• Contact Details
Nice to have
• A link to contact us directly for a free first trial class

```html
<!DOCTYPE html>
<html lang="en">
<head>
<meta charset="utf-8">
<title>Summit Bodyform Gym</title>
<link href="https://fonts.googleapis.com/css2?family=Open+Sans:wght@400;600;700&family=Roboto+Condensed:wght@700&display=swap" rel="stylesheet">
<style>
:root{
  --brand:#0792cd;
  --band:#12a0c6;
  --ink:#333;
  --muted:#6b6b6b;
  --footer:#2e2e2e;
  --footer-deep:#272727;
  --footer-text:#a9a9a9;
  --white:#fff;
}
*{margin:0;padding:0;box-sizing:border-box}
html,body{width:868px;height:1200px;overflow:hidden;background:var(--white)}
body{position:relative;font-family:"Open Sans",Arial,sans-serif;color:var(--ink)}
.abs{position:absolute}

/* header */
.site-header{position:absolute;left:0;top:0;width:868px;height:82px;border-top:2px solid var(--brand);background:var(--white)}
.brand{position:absolute;left:72px;top:18px;display:flex;align-items:center;gap:6px}
.brand-name{font-family:"Open Sans",Arial,sans-serif;font-weight:700;font-size:22px;color:#222;letter-spacing:-.3px}
.brand-dot{width:9px;height:9px;border-radius:50%;background:var(--brand)}
.main-nav{position:absolute;left:286px;top:34px;display:flex;gap:14.5px;font-size:8.6px;color:#444;letter-spacing:.1px}
.main-nav .is-active{color:var(--brand)}

/* hero */
.hero{position:absolute;left:0;top:82px;width:868px;height:359px;overflow:hidden;
  background:linear-gradient(100deg,#c9ced3 0%,#8fa3b2 30%,#2f6f9e 55%,#4a5663 75%,#2c3034 100%)}
.hero-card{position:absolute;left:126px;top:53px;width:269px;height:254px;background:var(--white)}
.hero-title{position:absolute;left:23px;top:30px;font-size:21px;font-weight:400;color:var(--brand);letter-spacing:.2px}
.hero-copy{position:absolute;left:23px;top:66px;width:232px;font-size:7.4px;line-height:15.5px;color:#555}
.hero-copy p+p{margin-top:6px}
.btn-trial{position:absolute;left:24px;top:181px;width:139px;height:28px;background:var(--brand);color:var(--white);
  font-size:8.8px;font-weight:600;display:flex;align-items:center;justify-content:center;box-shadow:0 2px 4px rgba(0,0,0,.25)}

/* features band */
.features{position:absolute;left:0;top:441px;width:868px;height:190px;background:var(--band)}
.feature{position:absolute;color:var(--white)}
.feature h3{font-size:14.5px;font-weight:400;position:absolute;left:42px;top:0;white-space:nowrap}
.feature p{font-size:7.4px;line-height:15px;position:absolute;left:42px;top:24px;width:270px}
.feature svg{position:absolute;left:0;top:0}

/* intro */
.intro-title{position:absolute;left:0;width:868px;top:655px;text-align:center;font-size:13.5px;color:var(--brand);font-weight:400}
.intro-sub{position:absolute;left:0;width:868px;top:686px;text-align:center;font-size:8.6px;color:var(--muted)}
.tile{position:absolute;top:722px;width:224px}
.tile-photo{width:224px;height:134px}
.tile-shadow{height:6px;margin:0 -10px;background:radial-gradient(ellipse at top,rgba(0,0,0,.15),rgba(0,0,0,0) 70%)}
.tile h4{text-align:center;margin-top:10px;font-size:11.2px;font-weight:400;color:#222}
.tile h4.is-link{color:var(--brand)}
.tile p{text-align:center;margin-top:6px;font-size:8px;line-height:15.5px;color:var(--muted)}

/* footer */
.site-footer{position:absolute;left:0;top:962px;width:868px;height:192px;background:var(--footer)}
.footer-col{position:absolute;top:30px}
.footer-col h5{font-size:10.2px;font-weight:700;color:var(--white);letter-spacing:.2px}
.footer-col ul{list-style:none;margin-top:9px}
.footer-col li{font-size:7.8px;color:var(--footer-text);line-height:18px}
.about p{font-size:7.8px;line-height:17px;color:var(--footer-text);width:245px;margin-top:10px}
.about-arrows{position:absolute;left:217px;top:0;font-size:9px;color:var(--footer-text);letter-spacing:3px}
.person{position:absolute;left:0;top:86px;display:flex;gap:12px;align-items:center}
.avatar{width:42px;height:42px;border-radius:50%;background:linear-gradient(135deg,#d9e4ea,#7fa9c2);border:2px solid #dfe6ea}
.person strong{display:block;font-size:8.6px;color:#25b3e0;font-weight:700}
.person span{display:block;font-size:8px;color:var(--footer-text);margin-top:5px}
.contact li{display:flex;align-items:center;gap:7px}
.bottom-bar{position:absolute;left:0;top:1154px;width:868px;height:46px;background:var(--footer-deep);
  display:flex;align-items:center;justify-content:center;font-size:7.8px;color:var(--footer-text)}
</style>
</head>
<body>

<header class="site-header">
  <div class="brand"><span class="brand-name">Summit</span><span class="brand-dot"></span></div>
  <nav class="main-nav">
    <span class="is-active">HOME</span><span>CLASS DESCRIPTIONS</span><span>GYM DESCRIPTION</span><span>CLASS SCHEDULES</span><span>TRAINER PROFILES</span><span>GYM PHILOSOPHY</span><span>CONTACT</span>
  </nav>
</header>

<section class="hero">
  <div class="abs" style="inset:0" role="img" aria-label="Gym interior with a wooden gymnastic ring hanging in the foreground"></div>
  <svg class="abs" style="left:0;top:0" width="868" height="359" viewBox="0 0 868 359">
    <polygon points="0,150 160,330 160,359 0,359" fill="rgba(255,255,255,.12)"/>
    <polygon points="330,0 470,0 220,359 80,359" fill="rgba(255,255,255,.08)"/>
    <polyline points="28,230 16,246 28,262" fill="none" stroke="rgba(255,255,255,.6)" stroke-width="1.5"/>
    <polyline points="840,230 852,246 840,262" fill="none" stroke="rgba(255,255,255,.6)" stroke-width="1.5"/>
  </svg>
  <div class="hero-card">
    <svg class="abs" style="left:0;top:0" width="269" height="254" viewBox="0 0 269 254">
      <polygon points="224,11 269,11 269,57" fill="var(--brand)"/>
      <polygon points="9,218 9,254 49,254" fill="var(--brand)"/>
    </svg>
    <h1 class="hero-title">SUMMIT GYM</h1>
    <div class="hero-copy">
      <p>At vero eos et accusamus et iusto odio dignissimos ducimus qui blanditiis praesentium voluptatum deleniti atque corrupti quos dolores et quas molestias excepturi sint occaecati cupiditate non provident, similique sunt in culpa qui officia</p>
      <p>Sed ut perspiciatis unde omnis iste natus error sit voluptatem accusantium doloremque</p>
    </div>
    <a class="btn-trial">FREE FIRST TRIAL CLASS &nbsp;&gt;&gt;</a>
  </div>
</section>

<section class="features">
  <div class="feature" style="left:70px;top:25px">
    <svg width="26" height="32" viewBox="0 0 26 32"><circle cx="18" cy="4" r="3.5" fill="#fff"/><path d="M16 9 L8 20 L4 31 M12 15 L22 12 M12 15 L14 31" stroke="#fff" stroke-width="3.5" fill="none" stroke-linecap="round"/></svg>
    <h3>On the other hand, we denounce</h3>
    <p>At vero eos et accusamus et iusto odio dignissimos ducimus qui blanditiis praesentium voluptatum deleniti atque corrupti quos dolores.,.</p>
  </div>
  <div class="feature" style="left:437px;top:25px">
    <svg width="26" height="32" viewBox="0 0 26 32"><circle cx="9" cy="9" r="7" fill="#fff"/><circle cx="9" cy="9" r="2.5" fill="var(--band)"/><path d="M9 16 L9 28 M9 20 L20 16" stroke="#fff" stroke-width="3.5" stroke-linecap="round"/></svg>
    <h3>Nam libero tempore, cum soluta nobis est</h3>
    <p>At vero eos et accusamus et iusto odio dignissimos ducimus qui blanditiis praesentium voluptatum deleniti atque corrupti quos dolores.,.</p>
  </div>
  <div class="feature" style="left:70px;top:105px">
    <svg width="28" height="30" viewBox="0 0 28 30"><path d="M6 24 L22 8" stroke="#fff" stroke-width="3.5"/><rect x="17" y="2" width="9" height="9" rx="1.5" transform="rotate(45 21.5 6.5)" fill="#fff"/><rect x="2" y="19" width="9" height="9" rx="1.5" transform="rotate(45 6.5 23.5)" fill="#fff"/></svg>
    <h3>On the other hand, we denounce</h3>
    <p>At vero eos et accusamus et iusto odio dignissimos ducimus qui blanditiis praesentium voluptatum deleniti atque corrupti quos dolores.,.</p>
  </div>
  <div class="feature" style="left:437px;top:105px">
    <svg width="28" height="32" viewBox="0 0 28 32"><circle cx="14" cy="6" r="5" fill="none" stroke="#fff" stroke-width="2.5"/><path d="M14 3 L14 6 L16 7" stroke="#fff" stroke-width="1.5" fill="none"/><rect x="3" y="14" width="22" height="3" fill="#fff"/><path d="M6 17 L6 29 M22 17 L22 29 M2 29 L26 29" stroke="#fff" stroke-width="3"/></svg>
    <h3>Nam libero tempore, cum soluta nobis est</h3>
    <p>At vero eos et accusamus et iusto odio dignissimos ducimus qui blanditiis praesentium voluptatum deleniti atque corrupti quos dolores.,.</p>
  </div>
</section>

<h2 class="intro-title">NAM LIBERO TEMPORE</h2>
<p class="intro-sub">On the other hand, we denounce with righteous indignation and dislike men who are so beguiled and demoralized...</p>

<article class="tile" style="left:73px">
  <div class="tile-photo" role="img" aria-label="Calisthenics rig with bars and ropes in the training hall" style="background:linear-gradient(180deg,#d8dadb,#8d9194 60%,#4d5256)"></div>
  <div class="tile-shadow"></div>
  <h4 class="is-link">CLASS DESCRIPTIONS</h4>
  <p>Lorem Ipsum is simply dummy text of the printing<br>and typesetting industry been the industry's<br>text ever since the 1500s...</p>
</article>
<article class="tile" style="left:322px">
  <div class="tile-photo" role="img" aria-label="Free weights area with wooden wall and plants" style="background:linear-gradient(180deg,#6b6a5a,#9a7a55 40%,#4b4a48 65%,#8a3e32)"></div>
  <div class="tile-shadow"></div>
  <h4>GYM DESCRIPTION</h4>
  <p>Lorem Ipsum is simply dummy text of the printing<br>and typesetting industry been the industry's<br>text ever since the 1500s...</p>
</article>
<article class="tile" style="left:571px">
  <div class="tile-photo" role="img" aria-label="Open studio floor with blue exercise mats" style="background:linear-gradient(180deg,#5d7d90,#9aa9b1 45%,#a14c3f 75%,#8d3c33)"></div>
  <div class="tile-shadow"></div>
  <h4>TRAINER PROFILES</h4>
  <p>Lorem Ipsum is simply dummy text of the printing<br>and typesetting industry been the industry's<br>text ever since the 1500s...</p>
</article>

<footer class="site-footer">
  <div class="footer-col about" style="left:73px">
    <h5>ABOUT US</h5>
    <span class="about-arrows">&lsaquo; &rsaquo;</span>
    <p>Lorem Ipsum is simply dummy text of the printing and typesetting industry. Lorem Ipsum has been the industry's standard dummy text ever since the 1500s...</p>
    <div class="person">
      <div class="avatar" role="img" aria-label="Member portrait"></div>
      <div><strong>Nam libero</strong><span>Business man</span></div>
    </div>
  </div>
  <div class="footer-col" style="left:409px">
    <h5>WELCOME</h5>
    <ul><li>Home</li><li>Class descriptions</li><li>Gym description</li><li>Class schedules</li><li>Trainer profiles</li></ul>
  </div>
  <div class="footer-col" style="left:545px">
    <h5>INFORMATION</h5>
    <ul style="line-height:20px"><li style="line-height:20px">Gym philosophy</li><li style="line-height:20px">Contact</li><li style="line-height:20px">Disclaimer</li><li style="line-height:20px">Sitemap</li></ul>
  </div>
  <div class="footer-col contact" style="left:690px">
    <h5>CONTACT INFO</h5>
    <ul>
      <li>120 Street name, City name,</li>
      <li>Country name : 60241 1111</li>
      <li style="margin-top:4px"><svg width="8" height="8" viewBox="0 0 10 10"><path d="M2 1 L4 1 L5 3.5 L3.8 4.5 Q5 6.5 6 6.5 L7 5.2 L9.5 6.2 L9.5 8.5 Q9 9.5 7.5 9.3 Q1 8 0.7 2.5 Q0.7 1 2 1Z" fill="var(--footer-text)"/></svg>( 1111 ) 1111 111</li>
      <li style="margin-top:4px"><svg width="9" height="7" viewBox="0 0 9 7"><rect width="9" height="7" fill="var(--footer-text)"/><path d="M0 0 L4.5 4 L9 0" stroke="var(--footer)" fill="none"/></svg>info@summitbodyform.com</li>
    </ul>
  </div>
</footer>
<div class="bottom-bar">© 2015. Summit Gym. All rights reserved</div>

</body>
</html>
```